New Interrior Decoration company needs new website

We need a website for our new company specialising in interior decoration to residential and commercial markets.
We supply and install decorative and printed films for office and home decoration such as feature walls.
We would like to keep the design simple and clean.

Target Market(s)

Architects and interior designaers

Industry/Entity Type

It Company

Number of Pages Required

5+ page

Font styles to use
Sans Serif

Requirements
Must have
• Home page,
• Services/products page (split into commercial and residential)
• Gallery (split into commercial and residential)
• contact form and page
Nice to have
• Very clean and minimalistic design.

```html
<!DOCTYPE html>
<html lang="en">
<head>
<meta charset="utf-8">
<title>Arden Interiors</title>
<link rel="stylesheet" href="https://fonts.googleapis.com/css2?family=Lato:wght@300;400;700&family=Open+Sans:ital,wght@0,400;0,600;1,700&display=swap">
<style>
:root{
  --blue:#0a5bbf;
  --blue-dark:#08489a;
  --ink:#2b2b2b;
  --grey-text:#8a8a8a;
  --light-bg:#ececec;
  --dark-bg:#1b1b1b;
  --white:#ffffff;
  --black:#050505;
}
*{box-sizing:border-box;margin:0;padding:0}
html,body{width:1200px;height:3495px;overflow:hidden}
body{position:relative;background:var(--white);font-family:"Open Sans",Arial,sans-serif;color:var(--ink)}
.abs{position:absolute}
.center{left:0;width:1200px;text-align:center}

/* hero */
.hero{top:0;left:0;width:1200px;height:650px;
  background:linear-gradient(180deg,#3a3c3b 0%,#4b4d4c 40%,#5e605f 70%,#cfd0d0 88%,#f2f2f2 100%)}
.call{top:22px;right:80px;display:flex;align-items:center;gap:14px;color:var(--white)}
.call small{display:block;font-size:16px;opacity:.85}
.call strong{display:block;font-family:"Lato",sans-serif;font-weight:400;font-size:30px;line-height:1}
.brand{top:193px;left:268px;height:127px;display:flex;align-items:center;gap:26px}
.brand .mark{width:127px;height:127px;background:var(--blue)}
.brand .name{font-family:"Lato",sans-serif;font-weight:700;font-size:70px;line-height:1;color:#262626;letter-spacing:1px}
.tagline{top:368px;color:var(--white);font-family:"Open Sans",sans-serif;font-style:italic;font-weight:700;font-size:40px;line-height:48px;text-transform:uppercase;text-shadow:0 2px 6px rgba(0,0,0,.5)}

/* nav */
.nav{top:650px;left:0;width:1200px;height:63px;background:var(--blue);display:flex;justify-content:center}
.nav a{display:block;height:63px;line-height:63px;padding:0 0;color:var(--white);text-decoration:none;font-family:"Open Sans",sans-serif;font-size:17px;text-transform:uppercase}
.nav .item{width:150px;text-align:center}
.nav .item.active{background:var(--black);width:114px;margin-right:30px}
.nav-shade{top:713px;left:0;width:1200px;height:44px}

/* headings */
.title{font-family:"Lato",sans-serif;font-weight:400;font-size:44px;line-height:1;text-transform:uppercase}
.title span{color:var(--blue)}
.copy{font-size:15px;line-height:27px;color:var(--grey-text)}
.btn{display:block;background:var(--blue);color:var(--white);font-family:"Lato",sans-serif;font-size:20px;text-transform:uppercase;text-align:center;border-radius:3px}

/* welcome */
.welcome-mark{top:776px;left:574px;width:52px;height:51px;background:var(--blue)}
.welcome-title{top:848px}
.welcome-copy{top:898px;left:140px;width:920px;text-align:center}
.welcome-btn{top:1048px;left:506px;width:188px;height:61px;line-height:61px}

/* services */
.services{top:1172px;left:0;width:1200px;height:571px;background:linear-gradient(180deg,#0d0d0d,#262626 60%,#1a1a1a)}
.services .title{color:var(--white)}
.services-title{top:1236px}
.services-copy{top:1298px;left:180px;width:840px;text-align:center;color:#dcdcdc}
.svc-img{top:1393px;height:163px}
.svc-img.left{left:186px;width:314px;background:linear-gradient(135deg,#b81e14,#6b1210 45%,#2e2e2e)}
.svc-img.right{left:722px;width:280px;background:linear-gradient(135deg,#e8e8e8,#9a9a9a 50%,#5a1010)}
.svc-divider{top:1380px;left:600px;width:1px;height:300px;background:#3a3a3a}
.svc-name{top:1576px;width:400px;text-align:center;color:var(--blue);font-family:"Lato",sans-serif;font-size:21px;text-transform:uppercase}
.svc-copy{top:1610px;width:400px;text-align:center;color:#d8d8d8;font-size:15px;line-height:27px}

/* testimonial */
.testimonial{top:1748px;left:0;width:1200px;height:270px;background:var(--light-bg)}
.testimonial-title{top:1808px;color:var(--ink)}
.avatar{top:1862px;left:212px;width:88px;height:88px;border-radius:50%;border:3px solid var(--white);box-shadow:0 0 0 2px #c8c8c8;background:radial-gradient(circle at 50% 40%,#e8d2b6,#c9a56e 60%,#7a8ea8)}
.quote{top:1876px;left:320px;width:680px;color:var(--grey-text);font-size:16px;line-height:27px}
.client{top:1940px;left:322px;font-family:"Lato",sans-serif;font-weight:700;font-size:14px;color:var(--blue);text-transform:uppercase;display:flex;align-items:center;gap:12px}
.client::before{content:"";width:22px;height:2px;background:var(--blue)}
.arrow{top:1880px;width:30px;height:50px}

/* gallery */
.gallery-title{top:2080px}
.filters{top:2144px;left:303px;display:flex;gap:11px}
.filters span{display:block;height:46px;line-height:44px;border:1px solid #9a9a9a;font-family:"Lato",sans-serif;font-size:18px;text-transform:uppercase;color:#555;text-align:center;border-radius:2px}
.filters .on{background:var(--blue);border-color:var(--blue);color:var(--white);width:84px}
.filters .c{width:250px}.filters .r{width:238px}
.tile{width:250px;height:176px}
.tile.featured{background:var(--blue);color:var(--white);display:flex;flex-direction:column;justify-content:center;align-items:center}
.tile.featured b{font-family:"Lato",sans-serif;font-weight:700;font-size:24px;text-transform:uppercase}
.tile.featured i{font-style:normal;font-size:16px;margin-top:4px}
.gallery-btn{top:2603px;left:506px;width:188px;height:58px;line-height:58px}

/* contact */
.contact{top:2726px;left:0;width:1200px;height:503px;background:linear-gradient(180deg,#161616,#232323 50%,#141414)}
.contact .title{color:#c9c9c9}
.contact-title{top:2786px}
.contact-copy{top:2844px;left:250px;width:700px;text-align:center;color:#d8d8d8}
.field{border:1px solid #6a6a6a;border-radius:3px;background:rgba(40,40,40,.85);color:#e0e0e0;font-size:14px;padding:12px 22px}
.submit{top:3110px;left:522px;width:156px;height:56px;line-height:56px}

/* footer */
.social{top:3276px;left:529px;display:flex;gap:11px}
.social span{width:40px;height:40px;border-radius:2px}
.social .s1{background:var(--blue)}.social .s2,.social .s3{background:#9a9a9a}
.foot-contact{top:3336px;font-size:14px;color:#555;line-height:24px}
.foot-contact a{color:var(--blue);text-decoration:none}
.to-top{top:3402px;left:585px;width:30px;height:30px;background:var(--black)}
.bottom-bar{top:3432px;left:0;width:1200px;height:63px;background:var(--black);color:var(--white);font-size:14px;line-height:63px;text-align:center}
.bottom-bar span{color:var(--blue)}
</style>
</head>
<body>

<header>
  <div class="abs hero" role="img" aria-label="Concrete feature wall with a white sofa on a light floor"></div>
  <div class="abs call">
    <svg width="34" height="34" viewBox="0 0 24 24" aria-hidden="true"><path fill="#0a5bbf" d="M6.6 10.8c1.4 2.8 3.8 5.1 6.6 6.6l2.2-2.2c.3-.3.7-.4 1-.2 1.1.4 2.3.6 3.6.6.6 0 1 .4 1 1V20c0 .6-.4 1-1 1C10.6 21 3 13.4 3 4c0-.6.4-1 1-1h3.5c.6 0 1 .4 1 1 0 1.3.2 2.5.6 3.6.1.3 0 .7-.2 1z"/></svg>
    <div><small>Call Us Know</small><strong>0400 218 736</strong></div>
  </div>
  <div class="abs brand">
    <div class="mark"></div>
    <div class="name">ARDEN<br>INTERIORS</div>
  </div>
  <h1 class="abs center tagline">We are specialising in interior decoration for<br>residential &amp; commercial markets.</h1>
</header>

<nav class="abs nav">
  <a class="item active" href="#">Home</a>
  <a class="item" href="#">About Us</a>
  <a class="item" href="#">Services</a>
  <a class="item" href="#">Gallery</a>
  <a class="item" href="#">Contact</a>
</nav>
<svg class="abs nav-shade" viewBox="0 0 1200 44" preserveAspectRatio="none" aria-hidden="true">
  <defs><radialGradient id="shade" cx="50%" cy="0%" r="60%"><stop offset="0" stop-color="#000" stop-opacity=".45"/><stop offset="1" stop-color="#000" stop-opacity="0"/></radialGradient></defs>
  <path d="M0 0 H1200 Q600 60 0 0Z" fill="url(#shade)"/>
</svg>

<section class="welcome">
  <div class="abs welcome-mark"></div>
  <h2 class="abs center title welcome-title">Welcome to <span>Arden Interiors</span></h2>
  <p class="abs copy welcome-copy">Lorem Ipsum is simply dummy text of the printing and typesetting industry. Lorem Ipsum has been the industry's standard dummy text ever since the 1500s, when an unknown printer took a galley of type and scrambled it to make<br>Lorem Ipsum is simply dummy text of the printing and typesetting industry. Lorem Ipsum has been the industry's standard dummy text ever since the 1500s, when an unknown printer took a galley of type and scrambled it to make a type specimen book. It has survived not only five centuries, but also the leap into electronic</p>
  <a class="abs btn welcome-btn" href="#">Know More</a>
</section>

<section>
  <div class="abs services" role="img" aria-label="Dim modern interior behind the services section"></div>
  <h2 class="abs center title services-title">Our <span>Services</span></h2>
  <p class="abs copy services-copy">Lorem Ipsum is simply dummy text of the printing and typesetting industry. Lorem Ipsum has been the industry's standard dummy text ever since the 1500s, when an unknown printer took a</p>
  <div class="abs svc-divider"></div>
  <div class="abs svc-img left" role="img" aria-label="Commercial lounge with red feature wall and colourful sofa"></div>
  <div class="abs svc-img right" role="img" aria-label="Cut-away view of a furnished residential apartment"></div>
  <h3 class="abs svc-name" style="left:143px">Commercial Design</h3>
  <h3 class="abs svc-name" style="left:662px">Residential Design</h3>
  <p class="abs svc-copy" style="left:143px">Lorem Ipsum is simply dummy text of the printing and typesetting industry. Lorem Ipsum has been the industry's standard..</p>
  <p class="abs svc-copy" style="left:662px">Lorem Ipsum is simply dummy text of the printing and typesetting industry. Lorem Ipsum has been the industry's standard..</p>
</section>

<section>
  <div class="abs testimonial"></div>
  <h2 class="abs center title testimonial-title">What our client say</h2>
  <svg class="abs arrow" style="left:128px" viewBox="0 0 30 50" aria-hidden="true"><path d="M24 4 6 25l18 21" fill="none" stroke="#9a9a9a" stroke-width="2"/></svg>
  <svg class="abs arrow" style="left:1042px" viewBox="0 0 30 50" aria-hidden="true"><path d="M6 4l18 21L6 46" fill="none" stroke="#9a9a9a" stroke-width="2"/></svg>
  <div class="abs avatar" role="img" aria-label="Client portrait"></div>
  <p class="abs quote">Lorem Ipsum is simply dummy text of the printing and typesetting industry. Lorem Ipsum has been the industry's standard dummy text ever since the 1500s</p>
  <div class="abs client">Client Name</div>
</section>

<section>
  <h2 class="abs center title gallery-title">Our <span>Gallery</span></h2>
  <div class="abs filters"><span class="on">All</span><span class="c">Commercial Design</span><span class="r">Residential Design</span></div>
  <div class="abs tile featured" style="top:2213px;left:79px"><b>Dream House</b><i>Residential</i></div>
  <div class="abs tile" style="top:2213px;left:345px;background:linear-gradient(135deg,#c9a45a,#8a6a3a 50%,#c2281e)" role="img" aria-label="Timber panel feature wall with red chair"></div>
  <div class="abs tile" style="top:2213px;left:608px;background:linear-gradient(135deg,#d8d8d8,#f0f0f0 50%,#b03030)" role="img" aria-label="White wall with red circle graphics"></div>
  <div class="abs tile" style="top:2213px;left:874px;background:linear-gradient(135deg,#d6e86a,#eef3c8 50%,#ffffff)" role="img" aria-label="Bright lounge with lime printed wall"></div>
  <div class="abs tile" style="top:2407px;left:79px;background:linear-gradient(135deg,#3fa3a8,#7cc6c4 50%,#8a5a3a)" role="img" aria-label="Office with dotted teal glass film"></div>
  <div class="abs tile" style="top:2407px;left:345px;background:linear-gradient(135deg,#5a6068,#8d9296 50%,#d5d5d5)" role="img" aria-label="Grey kitchen with pendant lights"></div>
  <div class="abs tile" style="top:2407px;left:608px;background:linear-gradient(135deg,#e9c040,#b88a30 50%,#f3f1ea)" role="img" aria-label="Retail interior with yellow shelving"></div>
  <div class="abs tile" style="top:2407px;left:874px;background:linear-gradient(180deg,#6a3a4a,#8a5560 60%,#e9e4de)" role="img" aria-label="Living room with plum feature wall"></div>
  <a class="abs btn gallery-btn" href="#">View All</a>
</section>

<section>
  <div class="abs contact" role="img" aria-label="Dark interior sketch behind the contact form"></div>
  <h2 class="abs center title contact-title">Get in <span>Touch</span></h2>
  <p class="abs copy contact-copy">Lorem Ipsum is simply dummy text of the printing and typesetting industry. Lorem Ipsum has been the industry's standard dummy text ever since the 1500s</p>
  <div class="abs field" style="top:2922px;left:93px;width:499px;height:51px">Name</div>
  <div class="abs field" style="top:2982px;left:93px;width:499px;height:52px">E-Mail</div>
  <div class="abs field" style="top:3045px;left:93px;width:499px;height:52px">Phone</div>
  <div class="abs field" style="top:2922px;left:608px;width:499px;height:175px">Message</div>
  <a class="abs btn submit" href="#">Submit</a>
</section>

<footer>
  <div class="abs social"><span class="s1"></span><span class="s2"></span><span class="s3"></span></div>
  <p class="abs center foot-contact">0 987 654 321 | <a href="#">info@ardeninteriors.example</a><br>Address: lorem ipsum is simple dummy text of print</p>
  <svg class="abs to-top" viewBox="0 0 30 30" aria-hidden="true"><path d="M9 14l6-6 6 6M9 21l6-6 6 6" fill="none" stroke="#0a5bbf" stroke-width="2"/></svg>
  <div class="abs bottom-bar">&copy;<span>ArdenInteriors</span> - 2016. All rights reserved.</div>
</footer>

</body>
</html>
```